Forex website redesign

We need an attractive good looking website design that increase the apatite of our visitors to subscribe to our advisory service, beside the fact that we do offer very high quality service.

Our service is where we connect to investor accounts who are subscribed, to automatically deliver and execute our advise to buy or sell straight onto their account using high tech software.

The final design should communicate financial safty and growth.
Updates

Here is something to keep in mind about our business model that may help you in your design, we SHOW people the right way to invest, so they can make money instead of going somewere else and lose it. Beside that point, most websites in forex that includes pictures of happy and excited people who make money ALWAY turn out to be scam. So please try not to position our business that way in visitor first impression once he/she visit our site.

Thank you for your help :)

Target Market(s)

Financial Market, 20-70 years old

Industry/Entity Type

Financial

Requirements
Must have
• Call to action feature + Logo redesign. Please visit www.veldoramarkets.com to get an idea of how we want it. Also include the personal photos of our advisors in your deign.

```html
<!DOCTYPE html>
<html lang="en">
<head>
<meta charset="utf-8">
<title>Veldora Markets LTD</title>
<link href="https://fonts.googleapis.com/css2?family=Source+Sans+3:ital,wght@0,400;0,600;0,700;1,400&display=swap" rel="stylesheet">
<style>
:root{
  --page:#eef0f2;
  --ink:#3a3a3a;
  --muted:#6b6b6b;
  --teal:#2a7f9e;
  --teal-light:#3fb1cf;
  --navy:#1d3d6b;
  --dark:#2b2b2b;
  --darker:#222;
  --white:#fff;
  --nav-top:#4a4a4a;
  --nav-bottom:#1f1f1f;
}
*{box-sizing:border-box;margin:0;padding:0}
html,body{width:1093px;height:1200px;overflow:hidden}
body{font-family:"Source Sans 3",sans-serif;color:var(--ink);background:var(--page);position:relative}
.hero-zone{position:absolute;left:0;top:0;width:1093px;height:515px;background:linear-gradient(#f7f8fa,#eceef1 70%,#dcdfe3 92%,#f6f7f8 96%,#e3e5e8)}
.brand{position:absolute;left:352px;top:28px;display:flex;align-items:center;gap:10px}
.brand-mark{width:52px;height:52px;background:var(--navy);border-radius:4px}
.brand-name{font-size:33px;font-weight:700;color:var(--navy);line-height:1}
.brand-tag{font-size:13px;font-weight:700;font-style:italic;color:var(--navy);margin-top:4px;letter-spacing:.2px}
.main-nav{position:absolute;left:173px;top:103px;width:748px;height:38px;background:linear-gradient(var(--nav-top),var(--nav-bottom));border-radius:3px;display:flex;justify-content:space-around;align-items:center;padding:0 14px}
.main-nav a{color:var(--white);font-size:10px;text-decoration:none;text-transform:uppercase}
.slider{position:absolute;left:172px;top:155px;width:749px;height:288px;background:#3a3a3a;border-radius:3px}
.slide{position:absolute;left:9px;top:8px;width:731px;height:272px;background:linear-gradient(90deg,#fff 0%,#f3f4f5 40%,#d8dadc 100%);overflow:hidden}
.slide-photo{position:absolute;right:0;top:0;width:420px;height:272px;background:linear-gradient(100deg,rgba(255,255,255,0) 0%,#b8b8b6 22%,#8d8a86 55%,#3f4246 100%)}
.slide-title{position:absolute;left:51px;top:32px;font-size:37px;font-weight:600;color:var(--teal);line-height:48px}
.slide-text{position:absolute;left:54px;top:126px;width:300px;font-size:8.6px;line-height:15.6px;color:#222}
.slide-btn{position:absolute;left:54px;top:197px;width:192px;height:39px;background:linear-gradient(var(--teal-light),#2789a8);color:var(--white);font-size:13px;font-weight:600;display:flex;align-items:center;justify-content:center;border-radius:2px}
.arrow{position:absolute;top:283px;width:26px;height:42px}
.arrow.left{left:159px}
.arrow.right{left:908px}
.shadow{position:absolute;left:260px;top:463px;width:640px;height:14px;border-radius:50%;background:radial-gradient(rgba(0,0,0,.35),rgba(0,0,0,0) 70%)}
.cta-band{position:absolute;left:0;top:515px;width:1093px;height:124px;background:var(--dark)}
.cta-band h2{position:absolute;left:164px;top:25px;font-size:19px;font-weight:600;color:var(--white)}
.cta-band p{position:absolute;left:166px;top:61px;width:610px;font-size:8.4px;font-style:italic;line-height:16px;color:#b5b5b5}
.cta-btn{position:absolute;left:800px;top:57px;width:126px;height:36px;background:linear-gradient(#f4f4f4,#cfcfcf);border-radius:2px;color:var(--teal);font-size:14px;display:flex;align-items:center;justify-content:center}
.section-title{position:absolute;left:166px;top:658px;font-size:16px;font-weight:600;color:var(--teal)}
.intro-photo{position:absolute;left:167px;top:695px;width:164px;height:88px;background:var(--white);border:1px solid #ddd;padding:6px}
.intro-photo div{width:100%;height:100%;background:linear-gradient(90deg,#9a9893,#5f6470 55%,#2a3142)}
.intro-text{position:absolute;left:349px;top:698px;width:580px;font-size:7.9px;line-height:14px;color:var(--muted)}
.card{position:absolute;top:810px;width:238px;height:289px;background:var(--white);border:1px solid #e2e2e2;border-radius:2px}
.card h3{text-align:center;margin-top:16px;font-size:16.5px;font-weight:400;color:var(--teal)}
.card-img{margin:12px auto 0;width:206px;height:106px}
.card p{margin:20px 0 0 19px;width:200px;font-size:8px;line-height:14px;color:var(--muted)}
.card-btn{position:absolute;left:19px;top:242px;width:114px;height:29px;background:linear-gradient(#4a4a4a,#1f1f1f);border-radius:2px;color:var(--white);font-size:10px;display:flex;align-items:center;justify-content:center}
.site-footer{position:absolute;left:0;top:1129px;width:1093px;height:71px;background:var(--darker)}
.footer-nav{position:absolute;left:168px;top:18px;display:flex;font-size:8px;color:#ddd}
.footer-nav span.sep{margin:0 14px}
.copyright{position:absolute;left:168px;top:40px;font-size:8px;color:#ddd}
.follow{position:absolute;left:770px;top:31px;font-size:8px;color:#ddd}
.social{position:absolute;left:821px;top:22px;display:flex;gap:3px}
.social span{width:25px;height:25px;border-radius:50%}
</style>
</head>
<body>
<header class="hero-zone">
  <div class="brand">
    <div class="brand-mark"></div>
    <div>
      <div class="brand-name">Veldora Markets LTD</div>
      <div class="brand-tag">From Traders to Traders, THE REAL DEAL</div>
    </div>
  </div>
  <nav class="main-nav">
    <a>Home</a><a>About Us</a><a>Order</a><a>Performance</a><a>Oren Castel Special</a><a>Terms &amp; Conditions</a><a>Why Us?</a><a>Contact Us</a>
  </nav>
  <div class="slider">
    <div class="slide">
      <div class="slide-photo" role="img" aria-label="Portrait photo of the advisor Mr. Halden in a suit beside a trading monitor"></div>
      <div class="slide-title">VELDORA MARKETS<br>MR. HALDEN</div>
      <p class="slide-text">is by far the ONLY signal provider on this planet who is NRB registered. He literally manages hundred of accounts value over $40 Million in total. He is a very reliable, trustworthy, talented and has a very deep understanding of the overall long term fundamental out-look in Forex.</p>
      <div class="slide-btn">CLICK HERE FOR MORE INFO</div>
    </div>
  </div>
  <svg class="arrow left" viewBox="0 0 26 42"><path d="M26 0 A21 21 0 0 0 26 42 Z" fill="#2a8fb0"/><path d="M15 16 L10 21 L15 26" stroke="#fff" stroke-width="2.5" fill="none"/></svg>
  <svg class="arrow right" viewBox="0 0 26 42"><path d="M0 0 A21 21 0 0 1 0 42 Z" fill="#2a8fb0"/><path d="M11 16 L16 21 L11 26" stroke="#fff" stroke-width="2.5" fill="none"/></svg>
  <div class="shadow"></div>
</header>

<section class="cta-band">
  <h2>LET US DO THE PICS, WHILE YOU ENJOY THE RIDE!</h2>
  <p>Furthermore, you can adjust the risk set-up according to your own risk tolerance (We provide excellent and fast customer support to answer any question you may have). Nevertheless, you can unsubscribe anytime you want. And you keep 100% of the profits on your account regardless. And with no obligation.</p>
  <div class="cta-btn">ORDER NOW</div>
</section>

<h2 class="section-title">HOW SIGNALS WORK</h2>
<div class="intro-photo"><div role="img" aria-label="Photo of the advisor in a dark suit in an office"></div></div>
<p class="intro-text">Once you subscribe, you will be re-directed to a secure page to download and set-up the EA copier on your VPS with all the instructions you need(We provide full support, and we can set it up for you for no additional charge. Once set-up, the software is of superior quality and copies flawlessly, and you have direct and total control over your account. Whereas your subscription will be renewed automatically by the end of the cycle you choose (Monthly/OR/4 months). Furthermore, you can adjust the risk set-up according to your own risk tolerance (We provide excellent and fast customer support to answer any question you may have). Neverthe-less, you can unsubscribe anytime you want. And you keep 100% of the profits on your account regardless. And with no obligation.</p>

<article class="card" style="left:168px">
  <h3>VeldoraFX Master</h3>
  <div class="card-img" role="img" aria-label="Blue illustration of a hand holding an alert symbol" style="background:linear-gradient(135deg,#0d5fb8,#3d9be6 50%,#0b57a8)"></div>
  <p>Mr. Halden is by far the ONLY signal provider on this planet who is NRB registered. He literally manages hundred of accounts value over $40 Million in total. He is a very reliable, trustworthy...</p>
  <div class="card-btn">READ MORE</div>
</article>
<article class="card" style="left:428px">
  <h3>VeldoraFX SafePlayer</h3>
  <div class="card-img" role="img" aria-label="Image of a hand touching floating screens beside server racks" style="background:linear-gradient(90deg,#1a1a1a,#8a8a8a 40%,#d9d9d9 55%,#2a2a2a)"></div>
  <p>Mr. Halden is by far the ONLY signal provider on this planet who is NRB registered. He literally manages hundred of accounts value over $40 Million in total. He is a very reliable, trustworthy...</p>
  <div class="card-btn">READ MORE</div>
</article>
<article class="card" style="left:689px">
  <h3>VeldoraFX Freedom</h3>
  <div class="card-img" role="img" aria-label="Digital illustration of a globe surrounded by network screens" style="background:radial-gradient(circle at 50% 45%,#4fa3e8,#0d3a80 55%,#061a3d)"></div>
  <p>Mr. Halden is by far the ONLY signal provider on this planet who is NRB registered. He literally manages hundred of accounts value over $40 Million in total. He is a very reliable, trustworthy...</p>
  <div class="card-btn">READ MORE</div>
</article>

<footer class="site-footer">
  <div class="footer-nav">
    <span>Home</span><span class="sep">|</span><span>About Us</span><span class="sep">|</span><span>Order</span><span class="sep">|</span><span>Performance</span><span class="sep">|</span><span>Oren Castel Special</span><span class="sep">|</span><span>Terms &amp; Conditions</span><span class="sep">|</span><span>Why Us?</span><span class="sep">|</span><span>Contact Us</span>
  </div>
  <div class="copyright">Copyrights© 2013. Veldora Markets. All rights Reserved.</div>
  <div class="follow">Follow Us :</div>
  <div class="social">
    <span style="background:#2f6db5"></span><span style="background:#3aa7dd"></span><span style="background:#2a7fb0"></span><span style="background:#444"></span>
  </div>
</footer>
</body>
</html>
```